Aunt Roula's Bakery

I am about to create a luxury boutique that specializes in cake baking and cupcake
and ready for parties and special events and order delivery
the logo has already made

Boutique

Email:auntroulasbakery@mailbox-example.net
Instagram: aunt_roula_bakery
Twitter: xxxxxxx
WhatsApp: xxxxxxx

Requirements
Must have
• luxury design

```html
<!DOCTYPE html>
<html lang="en">
<head>
<meta charset="utf-8">
<title>Aunt Roula's Bakery – Business Card</title>
<link rel="stylesheet" href="https://fonts.googleapis.com/css2?family=Quicksand:wght@500;700&display=swap">
<style>
  :root {
    --backdrop: #1b1b1b;
    --card-white: #ffffff;
    --slate: #7b7a74;
    --rose: #d996a8;
    --ink-light: #ffffff;
    --brand-grey: #7a7a75;
  }
  html, body {
    margin: 0;
    padding: 0;
    width: 1200px;
    height: 902px;
    overflow: hidden;
    background: var(--backdrop);
  }
  .canvas {
    position: relative;
    width: 1200px;
    height: 902px;
    font-family: 'Quicksand', sans-serif;
  }
  .business-card {
    position: absolute;
    left: 99px;
    top: 165px;
    width: 940px;
    height: 536px;
    transform: scale(0.96);
    transform-origin: top left;
    background: var(--card-white);
    overflow: hidden;
  }
  .card-panels {
    position: absolute;
    inset: 0;
    width: 940px;
    height: 536px;
  }
  .panel-rose { fill: var(--rose); }
  .panel-slate { fill: var(--slate); }

  .brand-name {
    position: absolute;
    left: 37px;
    top: 246px;
    width: 400px;
    margin: 0;
    text-align: center;
    color: var(--brand-grey);
    font-size: 36px;
    font-weight: 500;
    line-height: 1.2;
  }

  .contact-panel {
    position: absolute;
    left: 478px;
    top: 0;
    width: 462px;
    height: 536px;
    color: var(--ink-light);
    text-align: center;
  }
  .owner-name {
    position: absolute;
    top: 86px;
    width: 100%;
    margin: 0;
    font-size: 36px;
    font-weight: 700;
  }
  .owner-role {
    position: absolute;
    top: 124px;
    width: 100%;
    font-size: 22px;
    font-weight: 500;
    color: var(--rose);
  }
  .phone {
    position: absolute;
    top: 182px;
    width: 100%;
    font-size: 24px;
    font-weight: 500;
    letter-spacing: 1px;
  }
  .email {
    position: absolute;
    top: 220px;
    width: 100%;
    font-size: 19px;
    font-weight: 500;
  }
  .divider {
    position: absolute;
    left: 62px;
    width: 338px;
    height: 2px;
    background: var(--ink-light);
  }
  .divider-top { top: 259px; }
  .divider-bottom { top: 402px; }
  .social-list {
    position: absolute;
    top: 281px;
    left: 95px;
    margin: 0;
    padding: 0;
    list-style: none;
    text-align: left;
  }
  .social-item {
    display: flex;
    align-items: center;
    height: 33px;
    font-size: 22px;
    font-weight: 500;
  }
  .social-badge {
    width: 24px;
    height: 24px;
    margin-right: 10px;
    background: var(--rose);
  }
  .website {
    position: absolute;
    top: 413px;
    width: 100%;
    font-size: 23px;
    font-weight: 500;
  }
</style>
</head>
<body>
<main class="canvas">
  <section class="business-card" aria-label="Aunt Roula's Bakery business card">
    <svg class="card-panels" viewBox="0 0 940 536" aria-hidden="true">
      <path class="panel-rose" d="M442,0 C456,120 476,240 468,360 C461,440 441,500 420,536 L940,536 L940,0 Z"/>
      <path class="panel-slate" d="M449,0 C482,120 502,240 495,360 C489,440 470,500 448,536 L940,536 L940,0 Z"/>
    </svg>

    <p class="brand-name">Aunt Roula's Bakery</p>

    <div class="contact-panel">
      <h1 class="owner-name">Nadia Karam</h1>
      <div class="owner-role">Owner</div>
      <div class="phone">000 000 0000</div>
      <div class="email">auntroulasbakery@mailbox-example.net</div>
      <div class="divider divider-top"></div>
      <ul class="social-list">
        <li class="social-item"><span class="social-badge" aria-hidden="true"></span>aunt_roula_bakery</li>
        <li class="social-item"><span class="social-badge" aria-hidden="true"></span>aunt_roula_bakery</li>
        <li class="social-item"><span class="social-badge" aria-hidden="true"></span>aunt_roula_bakery</li>
      </ul>
      <div class="divider divider-bottom"></div>
      <div class="website">www.auntroulasbakery.example</div>
    </div>
  </section>
</main>
</body>
</html>
```